Pebble Hop - mobile play centre poster designs

Who are we - we are a mobile playground business that specialises in providing entertainment to children in a safe, clean environment either at home or in a function centre. Brief - create 4 different signs to be displayed on our playgrounds. Please find attached 3 photos from our competitors to use as a guide. Corflute sign - size A1 Toddler zone - size A1 Playground rules - size A4 No climbing - size 20cmx8cm sending through photos and documents now.
Colors
Designer to choose colors to be used in the design.
Requirements
Must have
- Colour, be very specific with the rules, pictures

```html
<!DOCTYPE html>
<html lang="en">
<head>
<meta charset="utf-8">
<title>Pebble Hop – Playground Rules</title>
<link rel="stylesheet" href="https://fonts.googleapis.com/css2?family=Anton&family=Source+Sans+3:wght@600;700&display=swap">
<style>
  :root {
    --backdrop: #e6e6e4;
    --band-light: #fbe65a;
    --band-deep: #f2d21a;
    --bamboo: #3f8f2e;
    --bamboo-light: #7cc04a;
    --bamboo-node: #2b6a1f;
    --panel-top: #ffffff;
    --panel-bottom: #fbf6d2;
    --rule-green: #1f7a2c;
    --accent-orange: #f18a1f;
    --heading-shadow: rgba(120, 70, 10, 0.35);
    --icon-fill: #d9d6c8;
    --foliage-deep: #2f7a2a;
    --foliage-light: #7ab84a;
  }
  * { box-sizing: border-box; margin: 0; padding: 0; }
  html, body {
    width: 895px; height: 1200px; overflow: hidden;
    background: var(--backdrop);
  }
  .poster {
    position: absolute; left: 37px; top: 20px;
    width: 820px; height: 1160px;
    background: repeating-linear-gradient(180deg,
      var(--band-light) 0 46px, var(--band-deep) 46px 92px);
    box-shadow: 0 6px 18px rgba(0,0,0,0.25);
  }
  .panel {
    position: absolute; left: 61px; top: 56px; right: 61px; bottom: 42px;
    background: linear-gradient(180deg, var(--panel-top) 0%, var(--panel-bottom) 70%, #f6efb8 100%);
  }
  .bamboo {
    position: absolute;
    background:
      repeating-linear-gradient(var(--dir), transparent 0 70px, var(--bamboo-node) 70px 74px),
      linear-gradient(var(--cross), var(--bamboo-node), var(--bamboo-light) 45%, var(--bamboo) 100%);
    border-radius: 6px;
  }
  .bamboo--top, .bamboo--bottom { left: 38px; right: 38px; height: 12px; --dir: 90deg; --cross: 180deg; }
  .bamboo--top { top: 32px; }
  .bamboo--bottom { bottom: 36px; }
  .bamboo--left, .bamboo--right { top: 28px; bottom: 30px; width: 12px; --dir: 180deg; --cross: 90deg; }
  .bamboo--left { left: 44px; }
  .bamboo--right { right: 44px; }

  .brand {
    position: absolute; top: 108px; left: 0; right: 0;
    display: flex; align-items: center; justify-content: center; gap: 22px;
  }
  .brand__name {
    font-family: "Source Sans 3", sans-serif; font-weight: 700;
    font-size: 84px; line-height: 1; color: var(--rule-green);
  }
  .brand__mark {
    width: 74px; height: 74px; border-radius: 50%;
    background: var(--accent-orange);
  }
  .notice {
    position: absolute; top: 272px; left: 80px; right: 80px;
    font-family: "Source Sans 3", sans-serif; font-weight: 700;
    font-size: 26px; line-height: 36px; text-align: center;
    color: var(--rule-green);
  }
  .title {
    position: absolute; top: 380px; left: 0; right: 0;
    font-family: "Anton", sans-serif; font-size: 80px; line-height: 1;
    text-align: center; letter-spacing: -1px;
    color: var(--accent-orange);
    text-shadow: 3px 4px 4px var(--heading-shadow);
  }
  .foliage {
    position: absolute; left: 20px; right: 20px; bottom: 0; height: 104px;
    background: linear-gradient(180deg, rgba(122,184,74,0) 0%, var(--foliage-light) 35%, var(--foliage-deep) 100%);
    border-radius: 60px 60px 0 0;
  }
  .rules {
    position: absolute; top: 518px; left: 119px; right: 40px;
    list-style: none;
  }
  .rule {
    display: flex; align-items: center; height: 62px;
  }
  .rule__icon {
    width: 104px; height: 52px; border-radius: 6px;
    background: var(--icon-fill); margin-right: 24px;
  }
  .rule__no {
    font-family: "Anton", sans-serif; font-size: 54px; line-height: 1;
    color: var(--accent-orange); width: 64px;
  }
  .rule__text {
    font-family: "Source Sans 3", sans-serif; font-weight: 700;
    font-size: 34px; color: var(--rule-green); white-space: nowrap;
  }
</style>
</head>
<body>
  <main class="poster">
    <div class="panel"></div>
    <div class="bamboo bamboo--top"></div>
    <div class="bamboo bamboo--bottom"></div>
    <div class="bamboo bamboo--left"></div>
    <div class="bamboo bamboo--right"></div>

    <header class="brand">
      <span class="brand__name">Pebble Hop</span>
      <span class="brand__mark"></span>
    </header>

    <p class="notice">Parents/Guardians must supervise children using<br>this play equipment at all times</p>

    <h1 class="title">PLAY GROUND RULES</h1>

    <div class="foliage" role="img" aria-label="Band of tropical jungle leaves along the bottom edge"></div>

    <ul class="rules">
      <li class="rule"><span class="rule__icon" role="img" aria-label="Icon of a pair of shoes"></span><span class="rule__no">NO</span><span class="rule__text">shoes – socks must be worn</span></li>
      <li class="rule"><span class="rule__icon" role="img" aria-label="Icon of a figure climbing a net"></span><span class="rule__no">NO</span><span class="rule__text">climbing the nets</span></li>
      <li class="rule"><span class="rule__icon" role="img" aria-label="Icon of a drink cup and burger"></span><span class="rule__no">NO</span><span class="rule__text">food or drink</span></li>
      <li class="rule"><span class="rule__icon" role="img" aria-label="Icon of a bottle and glass"></span><span class="rule__no">NO</span><span class="rule__text">bottles or glass</span></li>
      <li class="rule"><span class="rule__icon" role="img" aria-label="Icon of bubble gum being blown"></span><span class="rule__no">NO</span><span class="rule__text">chewing gum</span></li>
      <li class="rule"><span class="rule__icon" role="img" aria-label="Icon of a crossed knife and fork"></span><span class="rule__no">NO</span><span class="rule__text">sharp objects</span></li>
      <li class="rule"><span class="rule__icon" role="img" aria-label="Icon of a face paint palette and brush"></span><span class="rule__no">NO</span><span class="rule__text">face painting</span></li>
      <li class="rule"><span class="rule__icon" role="img" aria-label="Icon of a high-heeled shoe"></span><span class="rule__no">NO</span><span class="rule__text">stilettos</span></li>
    </ul>
  </main>
</body>
</html>
```